Business card for a Exhibition booth fabrication company

Hi. My company would like to change our corporate name card. We are an events and Exhibition stand builder company. We would like our corporate name card to resonate what we do. I need someone to create something unique that relates to the industry that I am in. The graphic designer should be creative to incorporate the elements of my industry and try to blend in well in the design of the card. Our aim is to ensure that we are unique and our card can look different from our competitors.
Updates

Target Market(s)

Marketing and events manager from all companies

Contact Information for Business Card

The business card should have the following details:
Name
Job Title
Email
Website

Colors

Designer to choose colors to be used in the design.

Requirements
Must have
• The card must be look something that is relevant to the service that I am providing. My website is: www.velmora-buildworks.com
• You can see my website to get more information on what service that I am doing
Nice to have
• On the back of my card, I would like to have a globe image with the incorporation of my company logo. This is to indicate that my services can be done in any part of the world.

```html
<!DOCTYPE html>
<html lang="en">
<head>
<meta charset="utf-8">
<title>Velmora Buildworks – Business Card</title>
<link rel="stylesheet" href="https://fonts.googleapis.com/css2?family=Jost:wght@400;500;600&family=Oswald:wght@400&display=swap">
<style>
  :root {
    --backdrop: #3a3a3c;
    --card: #141414;
    --card-edge: #1f1f1f;
    --red: #e3121b;
    --grey-text: #8a8a8a;
    --grey-light: #b5b5b5;
    --map-tone: #2c2c2c;
  }
  * { box-sizing: border-box; margin: 0; padding: 0; }
  html, body { width: 1200px; height: 1000px; overflow: hidden; }
  body {
    background: var(--backdrop);
    font-family: "Jost", sans-serif;
    position: relative;
  }
  .card {
    position: absolute;
    left: 270px;
    width: 660px;
    height: 380px;
    border-radius: 24px;
    background: linear-gradient(135deg, var(--card-edge), var(--card) 60%);
    overflow: hidden;
  }
  .card--front { top: 60px; }
  .card--back { top: 540px; }

  /* Front */
  .world-network {
    position: absolute;
    left: 70px; top: 30px;
    width: 540px; height: 300px;
    border-radius: 40px;
    background: radial-gradient(ellipse at 55% 50%, #3a3a3a 0%, var(--map-tone) 45%, rgba(20,20,20,0) 75%);
  }
  .brand-name {
    position: absolute;
    left: 0; right: 0; top: 160px;
    text-align: center;
    font-family: "Jost", sans-serif;
    font-weight: 500;
    font-size: 32px;
    letter-spacing: 4px;
    color: var(--grey-light);
  }
  .front-url {
    position: absolute;
    left: 0; right: 0; bottom: 42px;
    text-align: center;
    font-size: 17px;
    font-weight: 500;
    color: var(--grey-text);
  }
  .front-url .accent, .contact .accent { color: var(--red); }

  /* Back */
  .identity {
    position: absolute;
    right: 410px; top: 150px;
    text-align: right;
  }
  .identity__name {
    font-family: "Oswald", sans-serif;
    font-size: 34px;
    letter-spacing: 1px;
    color: #6f6f6f;
    line-height: 1.1;
  }
  .identity__title {
    font-size: 18px;
    font-weight: 600;
    color: var(--red);
  }
  .divider {
    position: absolute;
    left: 268px; top: 140px;
    width: 2px; height: 120px;
    background: var(--red);
  }
  .contact {
    position: absolute;
    left: 286px; top: 134px;
    list-style: none;
    font-size: 17px;
    line-height: 1.15;
    color: var(--grey-light);
  }
  .contact__label { color: var(--red); font-weight: 500; font-size: 15px; }
  .contact__row { display: flex; align-items: center; gap: 6px; }
  .contact__row svg { width: 15px; height: 15px; flex: none; }
  .contact__url { font-size: 17px; }
</style>
</head>
<body>

  <section class="card card--front">
    <div class="world-network" role="img" aria-label="World map with connected network lines linking locations"></div>
    <div class="brand-name">VELMORA BUILDWORKS</div>
    <div class="front-url">www.<span class="accent">velmora-buildworks</span>.com</div>
  </section>

  <section class="card card--back">
    <div class="identity">
      <div class="identity__name">MARCUS HALE</div>
      <div class="identity__title">President</div>
    </div>
    <div class="divider"></div>
    <ul class="contact">
      <li class="contact__label">Singapore Contact:</li>
      <li>+65 91840276</li>
      <li class="contact__label">Qatar Contact:</li>
      <li>+974 70528341</li>
      <li class="contact__row">
        <svg viewBox="0 0 16 16" aria-hidden="true"><rect x="1" y="3" width="14" height="10" rx="2" fill="var(--red)"/><path d="M2 4l6 5 6-5" stroke="#141414" stroke-width="1.4" fill="none"/></svg>
        info@velmora-buildworks.com
      </li>
      <li class="contact__row contact__url">
        <svg viewBox="0 0 16 16" aria-hidden="true"><circle cx="8" cy="8" r="7" fill="var(--red)"/><path d="M1 8h14M8 1c-3 3.5-3 10.5 0 14M8 1c3 3.5 3 10.5 0 14" stroke="#141414" stroke-width="1.1" fill="none"/></svg>
        www.<span class="accent">velmora-buildworks</span>.com
      </li>
    </ul>
  </section>

</body>
</html>
```